Looking for a modern, Professional business card design

We have a simple business card, but are looking for a more modern, professional look. A sample of the basic card is attached as well as the logo. We would also like to add that we offer:
Struggling with your finances?
- Learn to become debt free
- Discover the power of cash
- Control your money instead of it controlling you
Let us help you achieve a new level of financial freedom!
Also, we would like to have a "SPECIAL OFFER!: FREE 30 minute consultation"
Financial Planning

```html
<!DOCTYPE html>
<html lang="en">
<head>
<meta charset="utf-8">
<title>Northfield Financial Coaching – Business Card</title>
<link href="https://fonts.googleapis.com/css2?family=Open+Sans:ital,wght@0,400;0,600;0,700;1,700&display=swap" rel="stylesheet">
<style>
  :root {
    --stage: #000000;
    --paper: #ffffff;
    --ink: #222222;
    --green: #3f9b3c;
    --green-deep: #2f8a3a;
    --lime: #8dc63f;
    --grad-top: #8cc63e;
    --grad-bottom: #3a9443;
    --white: #ffffff;
  }
  * { box-sizing: border-box; margin: 0; padding: 0; }
  html, body {
    width: 1200px; height: 900px; overflow: hidden;
    background: var(--stage);
    font-family: "Open Sans", Arial, sans-serif;
  }
  .stage { position: relative; width: 1200px; height: 900px; }

  .card {
    position: absolute; top: 275px; width: 477px; height: 293px; overflow: hidden;
  }
  .card--front {
    left: 116px; background: var(--paper);
    border-radius: 0 46px 0 46px;
  }
  .card--back {
    left: 622px;
    border-radius: 46px 0 46px 0;
    background: linear-gradient(160deg, var(--grad-top) 0%, #6db33f 45%, var(--grad-bottom) 100%);
    color: var(--white);
  }

  /* front */
  .brand {
    position: absolute; left: 0; right: 0; top: 48px;
    display: flex; align-items: center; justify-content: center; gap: 10px;
  }
  .brand__dot { width: 16px; height: 16px; border-radius: 50%; background: var(--lime); }
  .brand__name {
    font-weight: 700; font-size: 22px; color: var(--green-deep); letter-spacing: 0.2px;
  }

  .contact {
    position: absolute; right: 229px; top: 146px; text-align: right; color: var(--ink);
  }
  .contact__name { font-size: 17px; font-weight: 600; color: var(--green); line-height: 22px; }
  .contact__role { font-size: 13px; line-height: 20px; margin-bottom: 9px; }
  .contact__line {
    display: flex; align-items: center; justify-content: flex-end; gap: 5px;
    font-size: 13px; line-height: 20px;
  }
  .contact__line svg { width: 10px; height: 10px; fill: var(--green); flex: none; }

  .offer { position: absolute; left: 280px; top: 163px; }
  .offer__label { font-size: 19px; color: var(--lime); line-height: 26px; }
  .offer__detail {
    font-size: 19px; font-weight: 700; font-style: italic; color: var(--green); line-height: 26px;
  }

  /* back */
  .emblem-area {
    position: absolute; right: -20px; top: 10px; width: 250px; height: 300px;
    background: radial-gradient(ellipse at 55% 45%, rgba(190,230,120,0.55) 0%, rgba(120,190,70,0.25) 45%, rgba(60,150,60,0) 72%);
  }
  .pitch { position: absolute; left: 21px; top: 34px; }
  .pitch__title {
    font-size: 26px; font-weight: 600; line-height: 38px;
    text-decoration: underline; text-decoration-thickness: 2px; text-underline-offset: 5px;
  }
  .pitch__list { list-style: none; margin-top: 12px; font-size: 13.5px; line-height: 20px; }
  .pitch__cta {
    margin-top: 25px; font-size: 14px; font-weight: 700; line-height: 22px; text-transform: uppercase;
  }
</style>
</head>
<body>
<main class="stage">

  <section class="card card--front" aria-label="Business card front">
    <div class="brand">
      <span class="brand__dot"></span>
      <span class="brand__name">Northfield Financial Coaching</span>
    </div>

    <div class="contact">
      <p class="contact__name">Daniel R. Hayes</p>
      <p class="contact__role">Personal Financial Coach</p>
      <p class="contact__line">(205) 555-0182
        <svg viewBox="0 0 24 24" aria-hidden="true"><path d="M6.6 10.8a15.1 15.1 0 0 0 6.6 6.6l2.2-2.2a1 1 0 0 1 1-.25 11.4 11.4 0 0 0 3.6.57 1 1 0 0 1 1 1V20a1 1 0 0 1-1 1A17 17 0 0 1 3 4a1 1 0 0 1 1-1h3.5a1 1 0 0 1 1 1c0 1.25.2 2.45.57 3.6a1 1 0 0 1-.25 1z"/></svg>
      </p>
      <p class="contact__line">daniel@steadymoneypath.com
        <svg viewBox="0 0 24 24" aria-hidden="true"><path d="M2 5h20v14H2z M3 6l9 7 9-7" fill="var(--green)"/><path d="M3.5 6.5 12 13l8.5-6.5" stroke="#fff" stroke-width="2" fill="none"/></svg>
      </p>
      <p class="contact__line">www.steadymoneypath.com
        <svg viewBox="0 0 24 24" aria-hidden="true"><circle cx="12" cy="12" r="11"/><path d="M1 12h22M12 1c4 4 4 18 0 22M12 1c-4 4-4 18 0 22" stroke="#fff" stroke-width="1.6" fill="none"/></svg>
      </p>
    </div>

    <div class="offer">
      <p class="offer__label">SPECIAL OFFER!:</p>
      <p class="offer__detail">FREE 30</p>
      <p class="offer__detail">minute consultation</p>
    </div>
  </section>

  <section class="card card--back" aria-label="Business card back">
    <div class="emblem-area" role="img" aria-label="Soft green brand emblem decoration"></div>
    <div class="pitch">
      <h2 class="pitch__title">Struggling with<br>your finances?</h2>
      <ul class="pitch__list">
        <li>Learn to become debt free</li>
        <li>Discover the power of cash</li>
        <li>Control your money</li>
        <li>instead of it&nbsp; controlling you</li>
      </ul>
      <p class="pitch__cta">Let us help you achieve a new<br>level of&nbsp; financial freedom!</p>
    </div>
  </section>

</main>
</body>
</html>
```